Real Estate Webpage Design

We have an existing website: ferndaleestatecollective.com.au
We focus customised service mainly on Property Management and second-hand property sales.
We are not entirely happy about the current design and layout can stay roughly the same as the back end coding is linked to a CRM system.
We would like to see the design are more reachable to our clients and appearing.
Please check our Website Design Draft for more details.

Industry/Entity Type

Real estate Agency

Number of Pages Required

5+ page

Font styles to use
Sans Serif

Colors

Designer to choose colors to be used in the design.

```html
<!DOCTYPE html>
<html lang="en">
<head>
<meta charset="utf-8">
<title>Ferndale Estate Collective</title>
<link href="https://fonts.googleapis.com/css2?family=Rajdhani:wght@600;700&family=Roboto:wght@400;500;700&display=swap" rel="stylesheet">
<style>
:root{
  --gold:#e3b441;
  --gold-soft:#d9b04a;
  --navy:#2b3a52;
  --navy-deep:#263449;
  --ink:#2a3346;
  --muted:#7b8190;
  --line:#e2e4e8;
  --white:#ffffff;
}
*{box-sizing:border-box;margin:0;padding:0}
html,body{width:1200px;height:4084px;overflow:hidden}
body{position:relative;font-family:"Roboto",Arial,sans-serif;color:var(--ink);background:var(--white)}
.abs{position:absolute}
.heading{font-family:"Rajdhani","Arial Narrow",sans-serif;font-weight:700;color:var(--ink);letter-spacing:.5px}
.btn-gold{background:var(--gold);color:var(--ink);font-weight:700;font-size:13px;display:flex;align-items:center;justify-content:center;text-transform:uppercase}
.photo{border-radius:0}

/* top bar */
.topbar{top:0;left:0;width:1200px;height:43px}
.topbar-contact{position:absolute;top:0;left:560px;height:43px;right:0;background:var(--navy);clip-path:polygon(30px 0,100% 0,100% 100%,0 100%);display:flex;align-items:center;padding-left:50px;gap:14px;color:#fff;font-size:13px}
.round{width:30px;height:30px;border-radius:50%;background:var(--gold);display:flex;align-items:center;justify-content:center}
.round.grey{background:#3e4c63;width:28px;height:28px}
.social{display:flex;gap:7px;margin-left:14px}
.header{top:43px;left:0;width:1200px;height:71px}
.brand{position:absolute;left:117px;top:-12px;display:flex;align-items:center;gap:12px}
.brand-mark{width:44px;height:44px;background:var(--gold)}
.brand-name{font-size:26px;font-weight:700;color:var(--gold)}
.nav{position:absolute;left:406px;top:26px;display:flex;gap:26px;font-size:13px;font-weight:500;color:var(--ink)}
.nav .active{color:var(--gold)}

/* hero */
.hero{top:114px;left:0;width:1200px;height:640px}
.hero-photo{position:absolute;inset:0;background:linear-gradient(120deg,#8fa6b8 0%,#d9dcdc 35%,#c98a5a 55%,#e9e8e4 75%,#f2f2f0 100%)}
.hero-box{position:absolute;left:301px;top:166px;width:595px;height:243px;background:rgba(255,255,255,.72);text-align:center}
.hero-box h1{font-size:42px;margin-top:28px}
.hero-box p{font-size:16px;font-weight:500;line-height:26px;margin:10px auto 0;width:470px}
.hero-box .btn-gold{width:146px;height:48px;margin:24px auto 0}
.slide-arrow{position:absolute;top:205px;width:18px;height:30px;background:rgba(255,255,255,.85);display:flex;align-items:center;justify-content:center}

/* about */
.about-photo-a{left:111px;top:820px;width:342px;height:385px;background:linear-gradient(160deg,#cfd9e2,#f4f4f2 45%,#4f5a5e 70%,#39a4c0 100%)}
.about-photo-b{left:345px;top:1025px;width:259px;height:185px;background:linear-gradient(150deg,#e8e8e6,#b9bcbd 60%,#8a8c8a);border:5px solid #fff}
.about-text{left:661px;top:826px;width:428px}
.about-text h2{font-size:32px}
.about-text p{font-size:13px;line-height:26px;color:var(--muted);text-align:justify;margin-top:16px}
.btn-outline{left:661px;top:1149px;width:140px;height:51px;border:3px solid var(--gold);display:flex;align-items:center;justify-content:center;font-weight:700;font-size:13px}

/* featured */
.featured{top:1293px;left:0;width:1200px;height:764px;background:var(--navy)}
.featured h2{position:absolute;top:40px;width:100%;text-align:center;font-size:34px;color:#fff}
.tab{position:absolute;top:107px;width:132px;height:49px;border:3px solid var(--gold);color:#fff;font-weight:700;font-size:13px;display:flex;align-items:center;justify-content:center}
.tab.on{background:var(--gold);color:var(--ink)}
.prop{position:absolute;top:194px;width:359px;height:470px;background:#fff;padding:7px}
.prop-photo{height:226px}
.prop-body{padding:20px 10px 0 10px}
.prop-title{font-weight:700;font-size:16px}
.prop-addr{font-size:14px;color:var(--muted);margin-top:8px;padding-bottom:12px;border-bottom:1px solid var(--line)}
.prop-specs{display:grid;grid-template-columns:1fr 1fr;row-gap:12px;padding:14px 0;border-bottom:1px solid var(--line);font-size:13px;color:var(--muted)}
.spec{display:flex;align-items:center;gap:10px}
.spec i{width:16px;height:14px;border:2px solid #b8bcc4;display:inline-block}
.prop-foot{display:flex;justify-content:space-between;align-items:center;margin-top:12px}
.prop-foot .btn-gold{width:138px;height:50px}
.price{font-weight:700;font-size:22px}
.dots{position:absolute;top:700px;left:563px;display:flex;gap:8px}
.dots span{width:12px;height:12px;border-radius:50%;background:#8d96a5}
.dots span.on{background:#fff}

/* blog */
.section-title{width:1200px;left:0;text-align:center;font-size:34px}
.post{top:2213px;width:309px;height:355px;background:#fff;box-shadow:0 4px 14px rgba(0,0,0,.1)}
.post-photo{height:214px;position:relative}
.post-date{position:absolute;left:0;top:0;width:60px;height:68px;background:var(--gold);font-weight:700;font-size:16px;text-align:center;padding-top:12px;line-height:24px}
.post h3{font-size:16px;font-weight:500;text-align:center;margin-top:22px;text-transform:uppercase}
.post p{font-size:13px;line-height:24px;color:var(--muted);text-align:center;padding:6px 18px 0}

/* contact */
.contact{top:2658px;left:0;width:1200px;height:607px;background:var(--gold-soft)}
.contact h2{position:absolute;top:40px;width:100%;text-align:center;font-size:40px;color:#fff}
.info{position:absolute;top:130px;display:flex;align-items:center;gap:28px;color:#fff;font-size:13px;line-height:22px}
.info b{display:block;font-size:14px;text-transform:uppercase}
.info-icon{width:80px;height:80px;border-radius:50%;background:#fff;display:flex;align-items:center;justify-content:center}
.field{position:absolute;background:#fff;font-size:14px;color:#7c7c7c;padding:16px 16px}
.send{position:absolute;left:518px;top:503px;width:164px;height:49px;background:var(--navy);color:#fff;font-weight:700;font-size:13px;display:flex;align-items:center;justify-content:center}

/* testimonials */
.quote{top:3424px;width:440px}
.quote p{font-size:13px;line-height:24px;color:var(--muted);text-align:justify}
.person{display:flex;align-items:center;gap:14px;margin-top:24px;position:relative}
.avatar{width:56px;height:56px;border-radius:50%;background:linear-gradient(135deg,#b9c1cc,#6d7686)}
.person b{font-size:14px}
.person small{font-size:12px}
.stars{color:var(--gold);font-size:11px;letter-spacing:2px;margin-top:4px}
.qmark{position:absolute;right:0;top:0;font-family:"Rajdhani",sans-serif;font-size:110px;line-height:80px;color:#e3e5e9;font-weight:700}
.t-arrow{top:3488px;width:20px;height:30px}

/* footer */
.footer-col{top:3800px;color:#fff}
.footer-col h4{font-size:17px;font-weight:700;text-transform:uppercase;margin-bottom:22px}
.links li{list-style:none;font-size:13px;display:flex;align-items:center;gap:20px;height:29px}
.links li::before{content:"";width:12px;height:12px;border-radius:50%;background:var(--gold)}
.newsletter{display:flex;width:326px;height:40px;background:#fff;align-items:center;padding:0 4px 0 16px;font-size:13px;color:#888;justify-content:space-between}
.newsletter span.btn-gold{width:96px;height:32px;font-size:11px}
.ci{display:flex;align-items:center;gap:20px;font-size:13px;line-height:22px;margin-bottom:12px}
.ci .round{width:44px;height:44px;background:#fff;border:none}
.copyright{top:4039px;left:111px;width:978px;border-top:1px solid #4a5870;text-align:center;color:#fff;font-size:12px;padding-top:10px}
.copyright b{color:var(--gold)}
</style>
</head>
<body>

<!-- top bar -->
<div class="abs topbar">
  <div class="topbar-contact">
    <span class="round"><svg width="14" height="14" viewBox="0 0 24 24"><path d="M6 2l4 4-2 3a12 12 0 0 0 7 7l3-2 4 4-3 4C10 22 2 14 2 5z" fill="#fff"/></svg></span>
    <span>+61 02 5550 1234</span>
    <span class="round" style="margin-left:22px"><svg width="14" height="14" viewBox="0 0 24 24"><rect x="3" y="7" width="18" height="13" fill="#fff"/><rect x="7" y="3" width="10" height="5" fill="#fff"/></svg></span>
    <span>02 5550 6789</span>
    <span class="social"><span class="round"></span><span class="round grey"></span><span class="round grey"></span><span class="round grey"></span></span>
  </div>
</div>

<!-- header -->
<header class="abs header">
  <div class="brand"><span class="brand-mark"></span><span class="brand-name">Ferndale</span></div>
  <nav class="nav">
    <span class="active">HOME</span><span>ABOUT US</span><span>LEASING</span><span>BUY</span><span>SELL</span><span>OUR TEAM</span><span>BLOG</span><span>CONTACT US &nbsp;&nbsp;|&nbsp;&nbsp; ENG ⌄</span>
  </nav>
</header>

<!-- hero -->
<section class="abs hero">
  <div class="hero-photo" role="img" aria-label="Bright modern living room with sofa, throw blanket and balcony view over water"></div>
  <div class="slide-arrow" style="left:0"><svg width="8" height="12"><path d="M7 1L2 6l5 5" stroke="var(--gold)" stroke-width="2" fill="none"/></svg></div>
  <div class="slide-arrow" style="right:0"><svg width="8" height="12"><path d="M1 1l5 5-5 5" stroke="var(--gold)" stroke-width="2" fill="none"/></svg></div>
  <div class="hero-box">
    <h1 class="heading">FERNDALE ESTATE COLLECTIVE</h1>
    <p>Ferndale means "the home, the house", buying a property is one of the most expensive</p>
    <div class="btn-gold">GET STARTED</div>
  </div>
  <svg class="abs" style="left:0;top:0" width="1200" height="640" viewBox="0 0 1200 640">
    <polygon points="0,472 600,632 1200,472 1200,640 0,640" fill="#fff"/>
    <polygon points="180,560 600,620 1020,560 1020,570 600,640 180,570" fill="var(--gold)"/>
  </svg>
</section>

<!-- about -->
<div class="abs photo about-photo-a" role="img" aria-label="White modern house with glass doors and pool"></div>
<div class="abs photo about-photo-b" role="img" aria-label="Furnished living room interior"></div>
<div class="abs about-text">
  <h2 class="heading">ABOUT FERNDALE</h2>
  <p>Ferndale means "the home, the house", buying a property is one of the most expensive expenses and important assets for people. Ferndale is a real estate company located in Ferndale, Canberra. Being a portfolio sales agent and property manager, coupled with our high–profile international real estate experience</p>
  <p style="margin-top:14px">Ferndale is considered a market leader on the cutting edge with deep industry knowledge, ranging from landlord–tenant relationships, residential purchases.</p>
</div>
<div class="abs btn-outline">LEARN MORE</div>

<!-- featured -->
<section class="abs featured">
  <h2 class="heading">FEATURED PROPERTIES</h2>
  <div class="tab" style="left:246px">FOR SALE</div>
  <div class="tab on" style="left:390px">FOR LEASE</div>
  <div class="tab" style="left:534px">OPEN TIMES</div>
  <div class="tab" style="left:678px">SOLD</div>
  <div class="tab" style="left:821px">LEASED</div>

  <article class="prop" style="left:37px">
    <div class="prop-photo" role="img" aria-label="Two-storey house with double garage and garden" style="background:linear-gradient(170deg,#4f86c9,#c9c6c0 50%,#8c7a6a)"></div>
    <div class="prop-body">
      <div class="prop-title">RED HILL</div>
      <div class="prop-addr">12 Harbor Lane Red Hill</div>
      <div class="prop-specs"><span class="spec"><i></i>4 Bedrooms</span><span class="spec"><i></i>2 Bathrooms</span><span class="spec"><i></i>3,414 Sqft</span><span class="spec"><i></i>2 Cars</span></div>
      <div class="prop-foot"><span class="btn-gold">VIEW DETAILS</span><span class="price">$1400 pw</span></div>
    </div>
  </article>
  <article class="prop" style="left:421px">
    <div class="prop-photo" role="img" aria-label="Apartment living room with city view" style="background:linear-gradient(160deg,#d9dde0,#a7aaa8 50%,#6a4e3a)"></div>
    <div class="prop-body">
      <div class="prop-title">BRADDON</div>
      <div class="prop-addr">104/6 Linden Street Braddon</div>
      <div class="prop-specs"><span class="spec"><i></i>4 Bedrooms</span><span class="spec"><i></i>2 Bathrooms</span><span class="spec"><i></i>3,414 Sqft</span><span class="spec"><i></i>2 Cars</span></div>
      <div class="prop-foot"><span class="btn-gold">VIEW DETAILS</span><span class="price">$560 pw</span></div>
    </div>
  </article>
  <article class="prop" style="left:808px">
    <div class="prop-photo" role="img" aria-label="Single-storey brick home with front path and lawn" style="background:linear-gradient(175deg,#3f7fd6,#9ec0e8 45%,#b7734e 65%,#6f8a4a)"></div>
    <div class="prop-body">
      <div class="prop-title">GRIFFITH</div>
      <div class="prop-addr">3 Marlow Street Griffith</div>
      <div class="prop-specs"><span class="spec"><i></i>4 Bedrooms</span><span class="spec"><i></i>2 Bathrooms</span><span class="spec"><i></i>3,414 Sqft</span><span class="spec"><i></i>3 Cars</span></div>
      <div class="prop-foot"><span class="btn-gold">VIEW DETAILS</span><span class="price">$1300 pw</span></div>
    </div>
  </article>
  <div class="dots"><span></span><span class="on"></span><span></span><span></span></div>
</section>

<!-- blog -->
<h2 class="abs heading section-title" style="top:2134px">LATEST BLOG</h2>
<article class="abs post" style="left:111px">
  <div class="post-photo" role="img" aria-label="Living room with sofa and large windows" style="background:linear-gradient(150deg,#e4e6e6,#b8b9b7 60%,#8c7b6b)"><div class="post-date">19<br>MAY</div></div>
  <h3>At vero eos et accusa</h3>
  <p>Et harum quidem rerum facilis est et expe dita distinctio nam libero tempore, cum soluta nobis est eligendiea.</p>
</article>
<article class="abs post" style="left:445px">
  <div class="post-photo" role="img" aria-label="Apartment buildings around a paved courtyard" style="background:linear-gradient(170deg,#2d6fd0,#a9c3de 40%,#8c8e8f)"><div class="post-date">19<br>MAY</div></div>
  <h3>At vero eos et accusa</h3>
  <p>Et harum quidem rerum facilis est et expe dita distinctio nam libero tempore, cum soluta nobis est eligendiea.</p>
</article>
<article class="abs post" style="left:780px">
  <div class="post-photo" role="img" aria-label="Open-plan living area with timber floor and staircase" style="background:linear-gradient(160deg,#d8d9db,#eeeeec 45%,#c0612f)"><div class="post-date">19<br>MAY</div></div>
  <h3>At vero eos et accusa</h3>
  <p>Et harum quidem rerum facilis est et expe dita distinctio nam libero tempore, cum soluta nobis est eligendiea.</p>
</article>

<!-- contact -->
<section class="abs contact">
  <h2 class="heading">CONTACT US</h2>
  <div class="info" style="left:160px">
    <span class="info-icon"><svg width="30" height="34" viewBox="0 0 24 28"><path d="M12 2a7 7 0 0 0-7 7c0 5 7 12 7 12s7-7 7-12a7 7 0 0 0-7-7z" fill="none" stroke="var(--navy)" stroke-width="2.4"/><circle cx="12" cy="9" r="2.5" fill="var(--navy)"/><ellipse cx="12" cy="24" rx="8" ry="2" fill="none" stroke="var(--navy)" stroke-width="2"/></svg></span>
    <div><b>Address:</b>18/7 Willow Crest Ave,<br>Ferndale, ACT, 2990</div>
  </div>
  <div class="info" style="left:514px">
    <span class="info-icon"><svg width="32" height="32" viewBox="0 0 24 24"><path d="M6 2l4 4-2 3a12 12 0 0 0 7 7l3-2 4 4-3 4C10 22 2 14 2 5z" fill="var(--navy)"/></svg></span>
    <div><b>Phone:</b>+61 02 5550 1234</div>
  </div>
  <div class="info" style="left:802px">
    <span class="info-icon"><svg width="36" height="26" viewBox="0 0 36 26"><rect width="36" height="26" rx="3" fill="var(--navy)"/><path d="M2 3l16 12L34 3" stroke="#fff" stroke-width="3" fill="none"/></svg></span>
    <div><b>Email:</b>hello@ferndaleestate.com</div>
  </div>
  <div class="field" style="left:235px;top:250px;width:359px;height:50px">First Name</div>
  <div class="field" style="left:605px;top:250px;width:360px;height:50px">Last Name</div>
  <div class="field" style="left:235px;top:312px;width:359px;height:50px">Your Phone</div>
  <div class="field" style="left:605px;top:312px;width:360px;height:50px">Your Email</div>
  <div class="field" style="left:235px;top:376px;width:730px;height:111px">Message</div>
  <div class="send">SEND MESSAGE</div>
</section>

<!-- testimonials -->
<h2 class="abs heading section-title" style="top:3346px">TESTIMONIALS</h2>
<svg class="abs t-arrow" style="left:42px" viewBox="0 0 20 30"><path d="M15 3L4 15l11 12" stroke="#c9ccd2" stroke-width="3" fill="none"/></svg>
<svg class="abs t-arrow" style="left:1140px" viewBox="0 0 20 30"><path d="M5 3l11 12L5 27" stroke="var(--gold)" stroke-width="3" fill="none"/></svg>
<div class="abs" style="left:600px;top:3430px;width:1px;height:120px;background:var(--line)"></div>
<div class="abs quote" style="left:111px">
  <p>Sophie is my best property manager! Always happy to response my queries and keep us well informed at all stage. &nbsp;I will definitely recommend her to my friends.</p>
  <div class="person"><span class="avatar" role="img" aria-label="Client portrait"></span><div><b>LIN MAO,</b> <small>Australia</small><div class="stars">★★★★★</div></div><span class="qmark">”</span></div>
</div>
<div class="abs quote" style="left:649px">
  <p>Very good service. Our property manager is very responsible, prompting and cares about detail. They use the system to track everything so no need to worry about miscommunication...</p>
  <div class="person"><span class="avatar" role="img" aria-label="Client portrait"></span><div><b>MIA CHEN,</b> <small>Australia</small><div class="stars">★★★★★</div></div><span class="qmark">”</span></div>
</div>

<!-- footer -->
<svg class="abs" style="left:0;top:3620px" width="1200" height="464" viewBox="0 0 1200 464">
  <polygon points="160,128 600,8 1040,128 1040,134 600,36 160,134" fill="var(--gold)"/>
  <polygon points="0,176 600,44 1200,176 1200,464 0,464" fill="var(--navy-deep)"/>
</svg>
<div class="abs footer-col" style="left:111px">
  <h4>Join our newsletter</h4>
  <div class="newsletter">Email Address<span class="btn-gold">JOIN NOW</span></div>
  <div style="display:flex;gap:8px;margin-top:20px"><span class="round"></span><span class="round grey"></span><span class="round grey"></span><span class="round grey"></span></div>
</div>
<div class="abs footer-col" style="left:483px">
  <h4>Quick links</h4>
  <ul class="links"><li>Home</li><li>About Us</li><li>Leasing</li><li>Buy</li><li>Sell</li><li>Our Team</li></ul>
</div>
<div class="abs footer-col" style="left:650px">
  <h4>Other</h4>
  <ul class="links"><li>Blog</li><li>Privacy Policy</li><li>Terms &amp; Conditions</li><li>Contact Us</li></ul>
</div>
<div class="abs footer-col" style="left:861px">
  <h4>Contact info</h4>
  <div class="ci"><span class="round"><svg width="16" height="20" viewBox="0 0 24 28"><path d="M12 2a7 7 0 0 0-7 7c0 5 7 12 7 12s7-7 7-12a7 7 0 0 0-7-7z" fill="var(--gold)"/></svg></span><span>18/7 Willow Crest Ave,<br>Ferndale, ACT, 2990</span></div>
  <div class="ci"><span class="round"><svg width="18" height="18" viewBox="0 0 24 24"><path d="M6 2l4 4-2 3a12 12 0 0 0 7 7l3-2 4 4-3 4C10 22 2 14 2 5z" fill="var(--gold)"/></svg></span><span>+61 02 5550 1234</span></div>
  <div class="ci"><span class="round"><svg width="18" height="18" viewBox="0 0 24 24"><rect x="3" y="7" width="18" height="13" fill="var(--gold)"/><rect x="7" y="3" width="10" height="5" fill="var(--gold)"/></svg></span><span>+61 02 5550 6789</span></div>
</div>
<div class="abs copyright">© 2022 <b>Ferndale</b> &nbsp;/&nbsp; All Rights Reserved</div>

</body>
</html>
```